MBRDC redesign and update stationary bc envelopes.

Stationary, Envelopes, Brochures, Business Card. Need to add second surgeon and two other offices. I need everything to match. I am a oral & maxillofacial surgeon.
Additional surgeon and three office addresses.
Jae Min Park, DMD, MD, INC

3718 Silver Meadow Parkway
El Dorado Hills, CA 95762

642 Lorin Way, Suite 101
Folsom, CA. 95630

2317 Vale Street, Suite 105
Auburn, CA. 95603
Updates

Logo design uploaded. Zapfino Extra/Adobe Garamond/Palatino are fonts used before. Not sure what is on exisiting stationary.

Target Market(s)

Referral dentist and sometimes patients. I am a oral & Maxillofacial surgeon.

Industry/Entity Type

Dental Clinic

Font styles to use
Serif
Script

Requirements
Must have
• Color of existing stationary. Update is possible.
Nice to have
• Conservative/modern
Should not have
• Playful

```html
<!DOCTYPE html>
<html lang="en">
<head>
<meta charset="utf-8">
<title>MBRDC Business Card</title>
<link rel="stylesheet" href="https://fonts.googleapis.com/css2?family=Montserrat:wght@400;500;700&family=Jost:wght@300&display=swap">
<style>
  :root {
    --bg: #ebe7e1;
    --card: #ffffff;
    --brown: #2e1205;
    --name: #2a1206;
    --green: #7b9b2f;
    --grey: #555555;
    --rule: #3a2a20;
  }
  html, body {
    margin: 0;
    padding: 0;
    width: 1200px;
    height: 1200px;
    overflow: hidden;
    background: var(--bg);
  }
  .canvas {
    position: relative;
    width: 1200px;
    height: 1200px;
  }
  .card {
    position: absolute;
    left: 120px;
    width: 960px;
    height: 548px;
    background: var(--card);
    border-radius: 26px;
    overflow: hidden;
    box-shadow: 0 6px 18px rgba(0,0,0,0.12);
  }
  .card-front { top: 32px; }
  .card-back { top: 620px; }

  .brand {
    position: absolute;
    right: 54px;
    top: 150px;
    display: flex;
    align-items: center;
    gap: 12px;
    font-family: "Montserrat", sans-serif;
    font-weight: 500;
    font-size: 38px;
    letter-spacing: 4px;
    color: var(--brown);
  }
  .brand-dot {
    width: 22px;
    height: 22px;
    border-radius: 50%;
    background: #d9df9f;
  }

  .surgeons {
    position: absolute;
    left: 58px;
    top: 250px;
    font-family: "Montserrat", sans-serif;
    color: var(--name);
  }
  .surgeon {
    margin: 0;
    font-weight: 700;
    font-size: 30px;
    line-height: 36px;
  }
  .surgeon .credentials {
    font-size: 17px;
    font-weight: 700;
  }
  .diplomate {
    margin: 4px 0 0;
    font-weight: 400;
    font-size: 20px;
    color: var(--green);
    letter-spacing: 0.3px;
  }
  .divider {
    position: absolute;
    left: 58px;
    top: 366px;
    width: 846px;
    height: 1px;
    background: var(--rule);
  }
  .office {
    position: absolute;
    top: 380px;
    margin: 0;
    font-family: "Montserrat", sans-serif;
    font-style: normal;
    font-size: 20px;
    line-height: 27px;
    color: var(--grey);
  }
  .office-eldorado { left: 60px; }
  .office-folsom { left: 380px; top: 384px; }
  .office-auburn { left: 702px; top: 384px; }

  .contact-band {
    position: absolute;
    left: 0;
    top: 484px;
    width: 100%;
    height: 40px;
    background: var(--brown);
    color: #ffffff;
    font-family: "Montserrat", sans-serif;
    font-size: 20px;
    line-height: 40px;
    text-align: center;
  }

  .landscape {
    position: absolute;
    left: 0;
    top: 0;
    width: 100%;
    height: 420px;
    background:
      radial-gradient(ellipse 70% 55% at 55% 45%, #d6dea0 0%, rgba(214,222,160,0) 70%),
      radial-gradient(ellipse 80% 35% at 50% 75%, #f1e3a4 0%, rgba(241,227,164,0) 75%),
      linear-gradient(180deg, #dfe9f1 0%, #eaf0ee 45%, #f6f1d8 75%, #ffffff 100%);
  }
  .services {
    position: absolute;
    left: 0;
    top: 420px;
    width: 100%;
    text-align: center;
    font-family: "Jost", sans-serif;
    font-weight: 300;
    font-size: 23px;
    line-height: 27px;
    color: var(--grey);
  }
  .services p { margin: 0; }
</style>
</head>
<body>
<div class="canvas">

  <section class="card card-front">
    <div class="brand"><span class="brand-dot"></span>MBRDC</div>

    <div class="surgeons">
      <p class="surgeon">Robert T. Hale, <span class="credentials">DDS, Inc</span></p>
      <p class="surgeon">Jae Min Park, <span class="credentials">DMD, MD, INC</span></p>
      <p class="diplomate">Diplomate of the American Board of Oral &amp; Maxillofacial Surgery</p>
    </div>

    <div class="divider"></div>

    <address class="office office-eldorado">3718 Silver Meadow<br>Parkway, El Dorado<br>Hills, CA 95762</address>
    <address class="office office-folsom">642 Lorin Way<br>Suite 101<br>Folsom, CA. 95630</address>
    <address class="office office-auburn">2317 Vale Street<br>Suite 105<br>Auburn, CA. 95603</address>

    <div class="contact-band">916.555.0142 | 916.555.0187| drhale@mbrdcoralsurgery.com</div>
  </section>

  <section class="card card-back">
    <div class="landscape" role="img" aria-label="Soft watercolour illustration of green mountains above golden rolling vineyard hills"></div>
    <div class="services">
      <p>Dentoalveolar Surgery| Dental Implant Surgery</p>
      <p>Orthognathic Surgery| Facial Trauma Surgery | Preprosthertic &amp; Reconstructive Surgery</p>
      <p>TMJ Disorders &amp; Surgery | Obstructive Sleep Apnea Surgery</p>
    </div>
  </section>

</div>
</body>
</html>
```